Simple Logo Design for Semi-Clear Plastic Frosted Card stock

Create a business card on frosted plastic. compliment existing logo elements with a tree trunk, roots, or seed at the lower half and the full logo both on the front.

Contact information will go on a solid portion of the back of this design since this card stock is semi-transparent.

It is important to consider this plastic card stock medium in your design. I found helpful tips and guides listed at vellaprint-sample.net: be careful to understand ink printed on plastic cards cannot have too much of a consistent print area or risks peeling and fine lines can easily scratch off.
Updates

2" x 3.5" 20PT Clear Plastic Business cards with Round corners Please get info or templates here: https://www.vellaprint-sample.net/product-detail/2-x-35-20pt-clear-plastic-business-cards-with-round-corners

Target Market(s)

Not for profit- religion

Industry/Entity Type

Business

Must include complementary elements to the existing logo

Font styles to use
Decorative

Colors
000000

Requirements
Must have
• Elements of community, nature and oneness. Such as: seed, roots, tree trunk, etc.
• Three lines of space on the back for Name, Title, Phone Number.
Nice to have
• I like a light use of decorative elements
Should not have
• No eyes, from faces or animals.

```html
<!DOCTYPE html>
<html lang="en">
<head>
<meta charset="utf-8">
<title>Steadfast Grove – Frosted Business Card</title>
<link rel="stylesheet" href="https://fonts.googleapis.com/css2?family=Cinzel:wght@400;700&family=Raleway:wght@400;500&display=swap">
<style>
  :root {
    --canvas-bg: #e3e8ed;
    --frost: rgba(255, 255, 255, 0.72);
    --frost-edge: rgba(255, 255, 255, 0.95);
    --forest: #1f4e3f;
    --leaf: #3f8a2f;
    --leaf-light: #6cae3c;
    --ink-dark: #2b3a33;
    --back-card: #1e5147;
    --back-card-deep: #163f37;
    --pale: #e9efec;
    --gold: #c9b27a;
  }
  * { margin: 0; padding: 0; box-sizing: border-box; }
  html, body { width: 800px; height: 1200px; overflow: hidden; }
  body {
    background: var(--canvas-bg);
    position: relative;
    font-family: "Raleway", sans-serif;
  }
  .card {
    position: absolute;
    left: 140px;
    width: 520px;
    height: 297px;
    border-radius: 18px;
    overflow: hidden;
  }
  .card-front {
    top: 170px;
    background: var(--frost);
    border: 1px solid var(--frost-edge);
    box-shadow: 0 6px 22px rgba(40, 60, 70, 0.15);
  }
  .card-back {
    top: 720px;
    background: linear-gradient(180deg, var(--back-card) 0%, var(--back-card-deep) 100%);
    box-shadow: 0 6px 22px rgba(20, 40, 35, 0.25);
  }
  .brand {
    position: absolute;
    left: 0; right: 0;
    text-align: center;
  }
  .card-front .brand { top: 64px; }
  .card-back .brand { top: 100px; }
  .brand-mark {
    display: inline-block;
    width: 22px; height: 22px;
    border-radius: 50%;
    background: var(--leaf);
    vertical-align: middle;
    margin-right: 10px;
  }
  .brand-name {
    font-family: "Raleway", sans-serif;
    font-weight: 500;
    font-size: 36px;
    letter-spacing: 1px;
    color: var(--forest);
    vertical-align: middle;
    text-transform: uppercase;
  }
  .card-back .brand-name { color: var(--pale); }
  .card-back .brand-mark { background: var(--leaf-light); }
  .tagline {
    margin-top: 6px;
    font-family: "Cinzel", serif;
    font-size: 11.5px;
    letter-spacing: 1.2px;
    color: var(--leaf);
  }
  .card-back .tagline { color: var(--gold); }
  .holder {
    position: absolute;
    left: 38px;
    top: 182px;
    font-family: "Cinzel", serif;
    color: var(--ink-dark);
    text-align: right;
  }
  .holder-name { font-weight: 700; font-size: 16px; letter-spacing: 0.5px; }
  .holder-title { font-size: 11px; margin-top: 2px; }
  .contact {
    position: absolute;
    left: 232px;
    top: 182px;
    list-style: none;
    font-family: "Cinzel", serif;
    font-size: 10.5px;
    color: var(--ink-dark);
    line-height: 20px;
  }
  .contact li { display: flex; align-items: center; gap: 8px; }
  .contact svg { width: 10px; height: 10px; }
  .base-band {
    position: absolute;
    left: 0; right: 0; bottom: 0;
    height: 18px;
    background: linear-gradient(180deg, var(--leaf) 0%, var(--forest) 100%);
  }
  .card-back .base-band { background: linear-gradient(180deg, #2f6e36 0%, #245a2c 100%); }
</style>
</head>
<body>

  <section class="card card-front" aria-label="Card front">
    <div class="brand">
      <span class="brand-mark"></span><span class="brand-name">Steadfast Grove</span>
      <p class="tagline">WISDOM, FELLOWSHIP &amp; STILLNESS</p>
    </div>
    <div class="holder">
      <p class="holder-name">DANIEL WELLER</p>
      <p class="holder-title">Director</p>
    </div>
    <ul class="contact">
      <li>
        <svg viewBox="0 0 10 10" aria-hidden="true"><path d="M2 1 L4 1 L4.6 3 L3.5 3.8 Q4.5 5.8 6.2 6.5 L7 5.4 L9 6 L9 8 Q5.5 9 2.5 5.8 Q0.8 3.5 2 1 Z" fill="var(--ink-dark)"/></svg>
        +330 5550-0148
      </li>
      <li>
        <svg viewBox="0 0 10 10" aria-hidden="true"><rect x="0.8" y="2" width="8.4" height="6" fill="none" stroke="var(--ink-dark)" stroke-width="1"/><path d="M0.8 2 L5 5.3 L9.2 2" fill="none" stroke="var(--ink-dark)" stroke-width="1"/></svg>
        INFO@DANIELWELLER-MAIL.NET
      </li>
    </ul>
    <div class="base-band"></div>
  </section>

  <section class="card card-back" aria-label="Card back">
    <div class="brand">
      <span class="brand-mark"></span><span class="brand-name">Steadfast Grove</span>
      <p class="tagline">WISDOM, FELLOWSHIP &amp; STILLNESS</p>
    </div>
    <div class="base-band"></div>
  </section>

</body>
</html>
```